New Innovative Counselling and psychotherapy Service needs Business Card design

Keep it simple and professional. On one side, just company name and logo (perhaps in all blue) and maybe a tag line.

On other side (all white) my name and Qualifications in centre

Industry/Entity Type

Health And Wellness

Contact Information for Business Card

Dara Whelby
Counsellor & Psychotherapist
BSc (Psychol.), BA, Dip. (Couns. & Psych.), PG.Cert (CBT), FGTrK, ONRE

I will also require Mobile no, Email and web site address of which I'll pass on to final designer.

Font styles to use
Sans Serif

Requirements
Must have
• My Logo Only and please use the colours in logo that is in it.
Should not have
• Any other images

```html
<!DOCTYPE html>
<html lang="en">
<head>
<meta charset="utf-8">
<title>Brightward Lane – Business Card</title>
<link rel="stylesheet" href="https://fonts.googleapis.com/css2?family=Lato:ital,wght@0,400;1,400&display=swap">
<style>
  :root {
    --page-bg: #e6e9ec;
    --card-bg: #ffffff;
    --brand-blue: #41b3ec;
    --brand-green: #8fd14f;
    --ink-dark: #3a3a3a;
    --ink-light: #ffffff;
    --social-grey: #9aa3ab;
  }
  html, body {
    margin: 0;
    width: 1200px;
    height: 900px;
    overflow: hidden;
    background: var(--page-bg);
    font-family: "Lato", sans-serif;
  }
  .business-card {
    position: absolute;
    left: 111px;
    top: 148px;
    width: 978px;
    height: 605px;
    background: var(--card-bg);
    box-shadow: 0 6px 24px rgba(0,0,0,0.12);
    overflow: hidden;
  }
  .card-panel {
    position: absolute;
    inset: 0;
    width: 100%;
    height: 100%;
  }
  .contact-list {
    position: absolute;
    left: 50px;
    top: 232px;
    margin: 0;
    padding: 0;
    list-style: none;
    color: var(--ink-light);
    font-size: 26px;
    line-height: 36px;
  }
  .contact-list li {
    display: flex;
    align-items: center;
    gap: 8px;
  }
  .contact-icon {
    width: 18px;
    height: 18px;
    fill: var(--ink-light);
  }
  .practitioner {
    position: absolute;
    left: 50px;
    top: 390px;
    color: var(--ink-light);
  }
  .practitioner-name {
    margin: 0;
    font-size: 34px;
    font-weight: 400;
    line-height: 42px;
    text-transform: uppercase;
  }
  .practitioner-role {
    margin: 0;
    font-size: 26px;
    line-height: 34px;
  }
  .practitioner-qualifications {
    margin: 6px 0 0;
    font-size: 25px;
    font-style: italic;
    line-height: 35px;
  }
  .brand {
    position: absolute;
    left: 478px;
    top: 81px;
    display: flex;
    align-items: center;
    gap: 14px;
  }
  .brand-dot {
    width: 90px;
    height: 90px;
    border-radius: 50%;
    background: var(--brand-blue);
  }
  .brand-name {
    font-size: 44px;
    color: var(--ink-dark);
    letter-spacing: 0.5px;
  }
  .social-links {
    position: absolute;
    left: 705px;
    top: 514px;
    display: flex;
    gap: 13px;
  }
  .social-dot {
    width: 36px;
    height: 36px;
    border-radius: 50%;
    background: var(--social-grey);
  }
</style>
</head>
<body>
  <div class="business-card">
    <svg class="card-panel" viewBox="0 0 652 403" preserveAspectRatio="none" aria-hidden="true">
      <path d="M0,0 L10,0 Q330,40 372,403 L0,403 Z" fill="var(--brand-blue)"/>
      <path d="M10,0 Q330,40 372,403" fill="none" stroke="var(--brand-green)" stroke-width="5"/>
    </svg>

    <ul class="contact-list">
      <li>
        <svg class="contact-icon" viewBox="0 0 20 20"><path d="M3 7c0-2 3-3 7-3s7 1 7 3v2h-4V7.5H7V9H3z M5 10h10l1 6H4z"/></svg>
        086 5302 917
      </li>
      <li>
        <svg class="contact-icon" viewBox="0 0 20 20"><path d="M2 5h16v10H2z M3 6l7 5 7-5" stroke="var(--brand-blue)" stroke-width="1.2"/></svg>
        info@brightwardlane.com
      </li>
      <li>
        <svg class="contact-icon" viewBox="0 0 20 20"><circle cx="10" cy="10" r="8"/><path d="M6 7c2 0 2 2 4 2s1 3 3 3M12 4c0 2-2 2-1 4" stroke="var(--brand-blue)" stroke-width="1.4" fill="none"/></svg>
        www.brightwardlane.com
      </li>
    </ul>

    <div class="practitioner">
      <h1 class="practitioner-name">Dara Whelby</h1>
      <p class="practitioner-role">Counsellor &amp; Psychotherapist</p>
      <p class="practitioner-qualifications">BSc (Psychol.), BA,Dip. (Couns. &amp; Psych.),<br>PG.Cert (CBT), FGTrK, ONRE</p>
    </div>

    <div class="brand">
      <span class="brand-dot" aria-hidden="true"></span>
      <span class="brand-name">Brightward Lane</span>
    </div>

    <div class="social-links" aria-label="Social media links">
      <span class="social-dot"></span>
      <span class="social-dot"></span>
      <span class="social-dot"></span>
      <span class="social-dot"></span>
    </div>
  </div>
</body>
</html>
```